Quarrybend Marble & Tile Needs a Business Card

Attached you will find your logo, my photo and design guidelines for a new business card. The final design will need two separate files to create an embossed card. The cards will be printed by www.plinkprint.com (Instructions below)
Format is the Plink SQUARE card
Quarrybend Marble And Tile is a brick and mortar, retail stone and tile shop.
One the front:
Quarrybend Marble And Tile
Dorian Fesslock
Owner
24807 Hollis Verdant Blvd
Suite P & R
Charlotte, NC 28193
Cell: 704-583-7142
Web: www.QuarrybendMarbleAndTile.com
(Make each word of the domain a different or alternating color)
On the back;
Something that shows beautiful colorful tile
Follow the design guide closely please. For more information see this page that describes creating the spot gloss file: https://www.plinkprint.com/us/business-cards/design-guidelines-spot-gloss
The logo is what we would like to have raised spot glossed.
Format is the Plink SQUARE card. See attahced guidlines.

```html
<!DOCTYPE html>
<html lang="en">
<head>
<meta charset="utf-8">
<title>Quarrybend Marble &amp; Tile — Business Card</title>
<link rel="stylesheet" href="https://fonts.googleapis.com/css2?family=Cinzel:wght@500;600&family=Poppins:wght@400;600&display=swap">
<style>
  :root {
    --backdrop: #e4e4e4;
    --card: #fbfbfb;
    --navy: #1c2f3a;
    --slate: #3b4d5a;
    --rust: #a13e1f;
    --gold: #c98a2a;
    --bronze: #9a6417;
    --sage: #5c6b4d;
    --sand: #bfb3a0;
    --ink: #2a2a2a;
  }
  * { box-sizing: border-box; margin: 0; padding: 0; }
  html, body { width: 1200px; height: 889px; overflow: hidden; }
  body { background: var(--backdrop); position: relative; font-family: "Poppins", sans-serif; }

  .card {
    position: absolute;
    width: 560px;
    height: 320px;
    background: var(--card);
    box-shadow: 0 10px 30px rgba(0,0,0,.12);
    overflow: hidden;
  }
  .card--front { left: 30px; top: 170px; }
  .card--back  { left: 610px; top: 400px; }

  .mosaic-area {
    position: absolute;
    top: 0;
    height: 170px;
    border: 2px solid var(--bronze);
    border-top: none;
    background:
      linear-gradient(90deg,
        rgba(161,62,31,.85) 0%,
        rgba(191,179,160,.85) 18%,
        rgba(92,107,77,.85) 34%,
        rgba(28,47,58,.9) 50%,
        rgba(92,107,77,.85) 66%,
        rgba(191,179,160,.85) 82%,
        rgba(201,138,42,.85) 100%);
  }
  .card--front .mosaic-area { left: 6px; width: 268px; }
  .card--back  .mosaic-area { left: 230px; width: 300px; }

  .portrait {
    position: absolute;
    left: 306px; top: 0;
    width: 196px; height: 232px;
    border-radius: 0 0 14px 14px;
    background: linear-gradient(160deg, #22343f 0%, #1e2f3a 55%, #2c3a48 100%);
  }
  .identity {
    position: absolute;
    left: 286px; top: 240px;
    width: 236px;
    text-align: center;
  }
  .identity__name {
    font-family: "Cinzel", serif;
    font-weight: 600;
    font-size: 19px;
    color: var(--navy);
    letter-spacing: .5px;
  }
  .identity__role { font-size: 11px; color: var(--ink); }

  .contact {
    position: absolute;
    left: 30px; bottom: 24px;
    list-style: none;
    font-size: 11.5px;
    color: var(--ink);
    line-height: 1.35;
  }
  .contact li { display: flex; align-items: flex-start; gap: 8px; margin-top: 5px; }
  .contact svg { width: 11px; height: 11px; flex: none; margin-top: 2px; fill: var(--ink); }
  .contact__phone { font-weight: 600; font-size: 13px; }
  .web--rust { color: var(--rust); }
  .web--gold { color: var(--gold); }
  .web--ink  { color: var(--ink); }

  .brand {
    position: absolute;
    left: 48px; top: 206px;
    display: flex; align-items: center; gap: 18px;
  }
  .brand__mark { width: 46px; height: 46px; background: var(--navy); flex: none; }
  .brand__name {
    font-family: "Cinzel", serif;
    font-weight: 500;
    color: var(--navy);
    line-height: 1.1;
  }
  .brand__primary {
    display: block; font-size: 32px; letter-spacing: 6px;
    padding-bottom: 4px; border-bottom: 1px solid var(--bronze);
  }
  .brand__secondary { display: block; font-size: 13px; letter-spacing: 10px; margin-top: 5px; }
</style>
</head>
<body>

<section class="card card--front">
  <div class="mosaic-area" role="img" aria-label="Colourful mosaic tile pattern"></div>

  <div class="portrait" role="img" aria-label="Portrait photo of Dorian Fesslock"></div>

  <div class="identity">
    <p class="identity__name">DORIAN FESSLOCK</p>
    <p class="identity__role">Owner</p>
  </div>

  <ul class="contact">
    <li class="contact__phone">
      <svg viewBox="0 0 24 24"><path d="M6.6 10.8a15 15 0 0 0 6.6 6.6l2.2-2.2a1 1 0 0 1 1-.25 11.4 11.4 0 0 0 3.6.57 1 1 0 0 1 1 1V20a1 1 0 0 1-1 1A17 17 0 0 1 3 4a1 1 0 0 1 1-1h3.5a1 1 0 0 1 1 1 11.4 11.4 0 0 0 .57 3.6 1 1 0 0 1-.25 1z"/></svg>
      704-583-7142
    </li>
    <li>
      <svg viewBox="0 0 24 24"><circle cx="12" cy="12" r="9" fill="none" stroke="#2a2a2a" stroke-width="2"/><path d="M3 12h18M12 3c3 3 3 15 0 18M12 3c-3 3-3 15 0 18" fill="none" stroke="#2a2a2a" stroke-width="1.6"/></svg>
      <span><span class="web--rust">www.</span><span class="web--gold">Quarrybend</span><span class="web--rust">Marble</span><span class="web--gold">And</span><span class="web--rust">Tile</span><span class="web--ink">.com</span></span>
    </li>
    <li>
      <svg viewBox="0 0 24 24"><path d="M12 2a7 7 0 0 0-7 7c0 5.2 7 13 7 13s7-7.8 7-13a7 7 0 0 0-7-7zm0 9.5A2.5 2.5 0 1 1 12 6.5a2.5 2.5 0 0 1 0 5z"/></svg>
      <span>24807 Hollis Verdant Blvd<br>Suite P &amp; R Charlotte, NC 28193</span>
    </li>
  </ul>
</section>

<section class="card card--back">
  <div class="mosaic-area" role="img" aria-label="Colourful mosaic tile pattern"></div>

  <div class="brand">
    <span class="brand__mark"></span>
    <p class="brand__name">
      <span class="brand__primary">QUARRYBEND</span>
      <span class="brand__secondary">MARBLE &amp; TILE</span>
    </p>
  </div>
</section>

</body>
</html>
```